Web Design Project

I want customers to be able to book appointments to get their makeup done and make a deposit and also have a gallery where i put my portfolio images, i want it to be very simple yet elegant.

Target Market(s)

Women ranging from 18-40 that want to get their makeup done

Industry/Entity Type

Makeup

Font styles to use
Sans Serif
Decorative

Requirements
Nice to have
• easy scheduling option and option to pay service in full on website.

```html
<!DOCTYPE html>
<html lang="en">
<head>
<meta charset="utf-8">
<title>Makeup Artist — Book Appointments</title>
<link rel="stylesheet" href="https://fonts.googleapis.com/css2?family=Roboto+Condensed:wght@400;700&family=Arimo:wght@400;700&display=swap">
<style>
:root{
  --blue:#3289c6;
  --blue-deep:#2a77ad;
  --ink:#3a3a3a;
  --text:#4a4a4a;
  --muted:#777;
  --white:#fff;
  --cocoa:#3b312d;
  --cocoa-panel:#453a36;
  --cocoa-deep:#2f2724;
  --rule:#d8d8d8;
  --accent-pink:#e46a8a;
}
*{box-sizing:border-box;margin:0;padding:0}
html,body{width:1200px;height:3064px;overflow:hidden}
body{position:relative;background:var(--white);font-family:"Arimo",Arial,sans-serif;color:var(--text)}
.abs{position:absolute}
.head{font-family:"Roboto Condensed",Arial,sans-serif;font-weight:700;text-transform:uppercase}

/* top strip */
.top-strip{left:0;top:0;width:1200px;height:5px;background:linear-gradient(90deg,var(--blue) 0 401px,var(--ink) 401px 804px,var(--blue) 804px)}

/* header */
.logo{left:94px;top:62px;font-family:"Roboto Condensed",Arial,sans-serif;font-weight:700;font-size:50px;color:#555;letter-spacing:1px}
.nav{top:82px;left:0;width:1200px;height:20px}
.nav a{position:absolute;font-family:"Arimo",Arial,sans-serif;font-size:14px;color:#333;text-decoration:none;white-space:nowrap}
.nav a.current{color:var(--blue)}

/* hero */
.hero{left:0;top:146px;width:1200px;height:441px;background:linear-gradient(110deg,#2e6fa6 0%,#5aa6db 35%,#3e8cc6 60%,#67b2e2 80%,#2f73a8 100%)}
.hero-tag{background:#3b3b3b;color:var(--white);text-align:center;white-space:nowrap}
.tag-deposit{left:707px;top:266px;width:296px;height:56px;font-size:36px;line-height:56px}
.tag-book{left:605px;top:332px;width:500px;height:74px;font-size:54px;line-height:74px}
.btn-slant{clip-path:polygon(6% 0,100% 0,94% 100%,0 100%);text-align:center;color:var(--white)}
.hero-more{left:756px;top:416px;width:204px;height:54px;background:#3b3b3b;font-size:26px;line-height:54px}

/* section titles */
.boxed-title{border:2px solid #555;text-align:center;color:#444;font-size:25px}
.boxed-title.light{border-color:var(--white);color:var(--white)}

/* portfolio */
.portfolio-title{left:488px;top:656px;width:224px;height:54px;line-height:50px}
.portfolio-intro{left:120px;top:752px;width:960px;font-size:13px;line-height:24px;text-align:center;color:#555}
.portfolio-shot{top:863px;width:285px;height:388px}
.shot-1{left:128px;background:linear-gradient(160deg,#c9a99a,#8a5f4e 55%,#e5d6cf)}
.shot-2{left:457px;background:linear-gradient(160deg,#e7dccf,#a3806a 55%,#efe6dc)}
.shot-3{left:786px;background:linear-gradient(160deg,#c7b6a8,#8d6f5f 55%,#ddd2c9)}
.portfolio-more{left:493px;top:1348px;width:212px;height:54px;background:var(--blue);font-size:26px;line-height:54px}

/* reasons */
.reasons{left:0;top:1506px;width:1200px;height:639px;background:radial-gradient(circle at 30% 40%,#43372f,var(--cocoa) 60%)}
.reasons-title{left:439px;top:1591px;width:322px;height:53px;line-height:49px}
.reason{width:340px;height:170px}
.reason-num{position:absolute;left:0;top:0;width:44px;height:44px;background:var(--white);color:#333;font-size:34px;line-height:44px;text-align:center}
.reason-title{position:absolute;left:62px;top:8px;font-size:18px;color:var(--white);white-space:nowrap}
.reason-rule{position:absolute;left:62px;top:36px;width:44px;height:2px;background:var(--white)}
.reason-text{position:absolute;left:0;top:58px;width:320px;font-size:13px;line-height:20px;color:#e8e2df}
.reason-more{position:absolute;left:0;top:122px;font-size:15px;color:var(--white)}

/* voices & highlight */
.says-title{left:273px;top:2213px;width:258px;height:54px;line-height:50px}
.highlight-title{left:748px;top:2213px;width:283px;height:54px;line-height:50px}
.quote-name{left:158px;top:2364px;font-size:17px;color:#555}
.quote-rule{left:158px;top:2392px;width:80px;height:3px;background:var(--accent-pink)}
.quote-text{left:158px;top:2408px;width:290px;font-size:13px;line-height:20px;color:#555}
.quote-photo{left:470px;top:2331px;width:199px;height:219px;background:linear-gradient(160deg,#d9b79a,#8b5a3d 55%,#e9d8c8)}
.video{left:717px;top:2331px;width:345px;height:219px;background:linear-gradient(120deg,#6d6a6c,#b9a9a0 45%,#4e4a4c)}
.play{left:795px;top:2426px;width:50px;height:50px}

/* footer */
.footer{left:0;top:2617px;width:1200px;height:357px;background:radial-gradient(circle at 70% 50%,#43372f,var(--cocoa) 60%)}
.footer-col{top:2586px;width:340px;height:345px;background:var(--cocoa-panel)}
.footer-col .cap{height:110px;background:var(--blue);color:var(--white);font-size:26px;line-height:110px;text-align:center}
.footer-col.mid .cap{background:var(--blue-deep)}
.footer-col .dash{position:absolute;left:148px;top:150px;width:44px;height:2px;background:#ddd}
.footer-col .copy{position:absolute;left:40px;top:170px;width:260px;font-size:13px;line-height:20px;color:#e8e2df;text-align:center}
.footer-btn{position:absolute;left:100px;top:272px;width:132px;height:40px;border:2px solid #ddd;color:var(--white);font-size:14px;line-height:36px;text-align:center}
.news-line{position:absolute;left:20px;top:176px;width:300px;font-size:13px;color:#e8e2df;text-align:center}
.news-field{position:absolute;left:33px;top:214px;width:189px;height:36px;border:2px solid #ddd;background:var(--cocoa-panel)}
.news-send{position:absolute;left:222px;top:214px;width:74px;height:36px;background:#ddd;color:#333;font-size:15px;line-height:36px;text-align:center}
.news-copy{position:absolute;left:20px;top:268px;width:300px;font-size:13px;line-height:20px;color:#e8e2df;text-align:center}

/* bottom bar */
.bottom{left:0;top:2974px;width:1200px;height:90px;background:var(--cocoa-deep)}
.legal{left:94px;top:3013px;font-size:12px;color:#cfc8c4}
.legal b{color:var(--white)}
.bottom-links{top:3013px;left:0;width:1200px}
.bottom-links a{position:absolute;font-size:12px;color:#cfc8c4;text-decoration:none;white-space:nowrap}
.social{top:3006px;width:26px;height:26px}
.social.blue{background:#3b6fb6}
.social.sky{background:#2a9fd6}
.social.red{background:#c9302c}
</style>
</head>
<body>

<div class="abs top-strip"></div>

<header>
  <div class="abs logo">YOURLOGO</div>
  <nav class="abs nav">
    <a class="current" style="left:613px">HOME</a>
    <a style="left:682px">ABOUT ME</a>
    <a style="left:781px">MY SERVICES</a>
    <a style="left:901px">BLOG</a>
    <a style="left:973px">FAQs</a>
    <a style="left:1039px">CONTACT</a>
  </nav>
</header>

<section>
  <div class="abs hero" role="img" aria-label="Model with striking makeup framed by flowing blue fabric"></div>
  <div class="abs hero-tag head tag-deposit">Make Deposit</div>
  <div class="abs hero-tag head tag-book">Book Appointments</div>
  <div class="abs btn-slant head hero-more">Read More</div>
</section>

<section>
  <h2 class="abs boxed-title head portfolio-title">My Portfolio</h2>
  <p class="abs portfolio-intro">Lorem ipsum dolor sit amet rem eos illo omnis aut aperiam ab ipsam ipsa odit aut aperiam aut aspernatur veritatis unde sed enim accusantium laudantium<br>sunt perspiciatis ipsam sed doloremque ipsam dolores totam unde aut illo aut veritatis explicabo dicta quia dicta veritatis dicta sunt quasi eaque rem</p>
  <div class="abs portfolio-shot shot-1" role="img" aria-label="Portfolio portrait with soft natural makeup and side-swept hair"></div>
  <div class="abs portfolio-shot shot-2" role="img" aria-label="Portfolio portrait with knitted scarf and warm makeup"></div>
  <div class="abs portfolio-shot shot-3" role="img" aria-label="Portfolio portrait with glamorous eye makeup and pearl necklace"></div>
  <div class="abs btn-slant head portfolio-more">Read More</div>
</section>

<section>
  <div class="abs reasons" role="img" aria-label="Dark brown background with swirling ornamental pattern"></div>
  <h2 class="abs boxed-title light head reasons-title">What You Choose Me</h2>

  <div class="abs reason" style="left:94px;top:1705px"><span class="reason-num head">1</span><span class="reason-title head">Amet Voluptatem</span><span class="reason-rule"></span><p class="reason-text">Lorem ipsum dolor sit amet rem illo omnis aperiam ab ipsam ipsa odit aut aperiam aspernatur veritatis unde enim accusantium laudantium sunt</p><span class="reason-more head">Read More</span></div>
  <div class="abs reason" style="left:449px;top:1705px"><span class="reason-num head">2</span><span class="reason-title head">Amet Voluptatem</span><span class="reason-rule"></span><p class="reason-text">Lorem ipsum dolor sit amet rem illo omnis aperiam ab ipsam ipsa odit aut aperiam aspernatur veritatis unde enim accusantium laudantium sunt</p><span class="reason-more head">Read More</span></div>
  <div class="abs reason" style="left:804px;top:1705px"><span class="reason-num head">3</span><span class="reason-title head">Amet Voluptatem</span><span class="reason-rule"></span><p class="reason-text">Lorem ipsum dolor sit amet rem illo omnis aperiam ab ipsam ipsa odit aut aperiam aspernatur veritatis unde enim accusantium laudantium sunt</p><span class="reason-more head">Read More</span></div>
  <div class="abs reason" style="left:94px;top:1915px"><span class="reason-num head">4</span><span class="reason-title head">Amet Voluptatem</span><span class="reason-rule"></span><p class="reason-text">Lorem ipsum dolor sit amet rem illo omnis aperiam ab ipsam ipsa odit aut aperiam aspernatur veritatis unde enim accusantium laudantium sunt</p><span class="reason-more head">Read More</span></div>
  <div class="abs reason" style="left:449px;top:1915px"><span class="reason-num head">5</span><span class="reason-title head">Amet Voluptatem</span><span class="reason-rule"></span><p class="reason-text">Lorem ipsum dolor sit amet rem illo omnis aperiam ab ipsam ipsa odit aut aperiam aspernatur veritatis unde enim accusantium laudantium sunt</p><span class="reason-more head">Read More</span></div>
  <div class="abs reason" style="left:804px;top:1915px"><span class="reason-num head">6</span><span class="reason-title head">Amet Voluptatem</span><span class="reason-rule"></span><p class="reason-text">Lorem ipsum dolor sit amet rem illo omnis aperiam ab ipsam ipsa odit aut aperiam aspernatur veritatis unde enim accusantium laudantium sunt</p><span class="reason-more head">Read More</span></div>
</section>

<section>
  <h2 class="abs boxed-title head says-title">What They Says</h2>
  <h2 class="abs boxed-title head highlight-title">Highlights Product</h2>
  <div class="abs quote-name head">Maya Doe, 25 YO</div>
  <div class="abs quote-rule"></div>
  <p class="abs quote-text">Lorem ipsum dolor sit amet rem eos illo omnis aut aperiam ab ipsam ipsa odit aut aperiam aut aspernatur veritatis unde accusantium sunt perspiciatis ipsam sed doloremque ......</p>
  <div class="abs quote-photo" role="img" aria-label="Client portrait with long wavy hair"></div>
  <div class="abs video" role="img" aria-label="Video still of a makeup artist applying makeup to a client"></div>
  <svg class="abs play" viewBox="0 0 50 50" aria-hidden="true"><circle cx="25" cy="25" r="25" fill="#fff"/><path d="M20 15 L36 25 L20 35 Z" fill="#555"/></svg>
</section>

<footer>
  <div class="abs footer" role="img" aria-label="Dark brown background with swirling ornamental pattern"></div>

  <div class="abs footer-col" style="left:97px">
    <h3 class="cap head">About Us</h3>
    <span class="dash"></span>
    <p class="copy">Lorem ipsum dolor sit amet &nbsp;omnis aperiam ab ipsam ipsa odit aut aperiam aspernatur veritatis unde enim accusantium laudantium</p>
    <span class="footer-btn head">Read More</span>
  </div>
  <div class="abs footer-col mid" style="left:431px">
    <h3 class="cap head">Company Address</h3>
    <span class="dash"></span>
    <p class="copy">Lorem ipsum dolor sit amet &nbsp;omnis aperiam ab ipsam ipsa odit aut aperiam aspernatur veritatis unde enim accusantium laudantium</p>
    <span class="footer-btn head">Read More</span>
  </div>
  <div class="abs footer-col" style="left:771px;width:332px">
    <h3 class="cap head">Newsletter</h3>
    <span class="dash"></span>
    <p class="news-line">Lorem ipsum dolor sit amet &nbsp;omnis aperiam</p>
    <span class="news-field"></span>
    <span class="news-send head">Send</span>
    <p class="news-copy">ab ipsam ipsa odit aut aperiam aspernatur veritatis unde enim accusantium laudantium</p>
  </div>

  <div class="abs bottom"></div>
  <p class="abs legal">© 2014 <b>YOUR COMPANY</b>. ALL RIGHTS RESERVED.</p>
  <nav class="abs bottom-links">
    <a style="left:449px">ABOUT US</a>
    <a style="left:530px">TERM AND USE</a>
    <a style="left:636px">PRIVACY POLICY</a>
    <a style="left:755px">FAQS</a>
    <a style="left:806px">CONTACT US</a>
  </nav>
  <span class="abs social blue" style="left:923px"></span>
  <span class="abs social sky" style="left:958px"></span>
  <span class="abs social red" style="left:994px"></span>
  <span class="abs social blue" style="left:1030px"></span>
  <span class="abs social red" style="left:1066px"></span>
</footer>

</body>
</html>
```